Stretch on the Green with Mira

I want to advertise my Stretch on the Green classes for Summer. Classes are outside at the lovely local park. Tolmore field. 12 Rawhiti St. Sandringham.
Classes are for beginners to advance levels.
Classes start Monday, October 17th.
Monday 6pm Beginners
Tuesday 6pm Intermediate
Thursday 6pm Intermediate/Advance
Saturday 9am All fitness levels
My Pilates classes are specially designed to help improve strength and flexibility but as well will also improve posture, reduce stress and develop control and endurance in the entire body.
Booking essential. Limited numbers so I can make sure the correct technique is always being followed.
For more info or to book contact details:
Mira 027385116
mira@stretchwithmira.net
www.stretchwithmira.net
$15 Per Session

Target Market(s)

Males and Females ages 35plus.

Industry/Entity Type

Fitness

Font styles to use
Sans Serif

Requirements
Must have
• My logo. Contact details. A Park that looks lovely to exercise at.
Nice to have
• Summer looking. Trees - inspiration to be exercising outside

```html
<!DOCTYPE html>
<html lang="en">
<head>
<meta charset="utf-8">
<title>Stretch on the Green with Mira</title>
<link rel="stylesheet" href="https://fonts.googleapis.com/css2?family=Playfair+Display:wght@700;900&family=Montserrat:wght@400;500;600;700;800&family=Dancing+Script:wght@700&display=swap">
<style>
:root{
  --pink:#d2769f;
  --pink-text:#cf6a97;
  --dark:#3a3a3c;
  --grey:#9c9c9e;
  --card:#dcdcdd;
  --ink:#1f1f21;
  --white:#ffffff;
}
*{box-sizing:border-box;margin:0;padding:0}
html,body{width:783px;height:1200px;overflow:hidden;background:var(--white)}
body{font-family:"Montserrat",Arial,sans-serif;color:var(--ink)}
.flyer{position:relative;width:783px;height:1200px;overflow:hidden;background:var(--white)}

/* hero */
.hero{position:absolute;left:0;top:0;width:783px;height:552px}
.hero-bg{position:absolute;left:0;top:0}
.brand{position:absolute;top:58px;left:0;width:100%;display:flex;flex-direction:column;align-items:center;gap:10px}
.brand-dot{width:34px;height:34px;border-radius:50%;background:#8d8d90}
.brand-name{font-family:"Montserrat",Arial,sans-serif;font-weight:500;font-size:19px;letter-spacing:2px;text-transform:uppercase;color:var(--pink)}
.title{position:absolute;top:160px;left:0;width:100%;text-align:center;font-family:"Playfair Display",Georgia,serif;font-weight:900;text-transform:uppercase;line-height:1}
.title-line1{display:block;font-size:68px;color:var(--dark);letter-spacing:-1px}
.title-line2{display:block;font-size:54px;color:var(--pink);letter-spacing:-1.5px;margin-top:2px}
.title-script{display:block;font-family:"Dancing Script",cursive;font-weight:700;text-transform:none;font-size:40px;color:var(--dark);margin-top:-2px;padding-left:30px;letter-spacing:0}

/* levels */
.levels{position:absolute;top:570px;left:0;width:100%;text-align:center;font-family:"Playfair Display",Georgia,serif;font-weight:700;text-transform:uppercase;line-height:1.12}
.levels-top{display:block;font-size:28px;color:var(--pink-text);letter-spacing:-.5px}
.levels-bottom{display:block;font-size:28px;color:var(--ink);letter-spacing:-.5px}
.rule{position:absolute;top:656px;left:150px;width:483px;height:1px;background:#bdbdbf}
.rule::after{content:"";position:absolute;left:212px;top:-1px;width:60px;height:3px;background:var(--pink)}
.start{position:absolute;top:672px;left:0;width:100%;text-align:center;font-size:28px;font-weight:700;color:var(--ink)}
.start em{font-style:normal;color:var(--pink-text)}

/* schedule */
.schedule{position:absolute;top:728px;left:31px;width:724px;display:flex;gap:13px}
.day{position:relative;flex:1;padding-top:8px}
.rings{position:absolute;top:0;left:0;width:100%;display:flex;justify-content:center;gap:11px;z-index:2}
.rings span{width:5px;height:14px;border:1.5px solid #5a5a5c;border-radius:3px;background:var(--white)}
.day-head{height:38px;border-radius:9px 9px 0 0;display:flex;align-items:flex-end;justify-content:center;padding-bottom:5px;font-size:19px;font-weight:600;color:var(--white);letter-spacing:.5px;text-transform:uppercase}
.day-head.is-pink{background:var(--pink)}
.day-head.is-dark{background:var(--dark)}
.day-body{height:108px;background:var(--card);border-radius:0 0 11px 11px;text-align:center;padding-top:6px}
.day-time{font-size:22px;font-weight:700;color:#333;padding-bottom:6px;margin:0 14px;border-bottom:1px solid #a9a9ab}
.day-level{height:58px;display:flex;align-items:center;justify-content:center;font-size:19px;font-weight:600;color:#333;line-height:1.1}
.day-level.is-small{font-size:16px}

.about{position:absolute;top:915px;left:40px;width:703px;text-align:center;font-size:10.5px;font-weight:700;line-height:1.35;color:var(--ink)}
.rule-thin{position:absolute;top:957px;left:31px;width:722px;height:1px;background:#bdbdbf}

/* offer */
.offer{position:absolute;top:970px;left:31px;width:730px;height:100px;display:flex}
.booking{width:335px;padding-top:4px}
.booking h2{font-size:21px;font-weight:700;color:var(--pink-text);letter-spacing:.5px}
.booking p{font-size:15px;font-weight:600;line-height:1.3;margin-top:4px}
.divider{width:0;border-left:1.5px dashed #777;margin:8px 0 10px}
.price{width:190px;text-align:center}
.price-amount{display:block;font-size:64px;font-weight:800;color:var(--pink-text);line-height:1;letter-spacing:-2px;margin-top:6px}
.price-unit{display:block;font-size:17px;font-weight:600;margin-top:4px}
.place{padding-left:28px;padding-top:4px;line-height:1.1}
.place b{display:block;font-size:17px;font-weight:700}
.place span{display:block;font-size:17px;font-weight:500}
.place strong{display:block;font-size:21px;font-weight:800;color:var(--pink-text);text-transform:uppercase;letter-spacing:.5px}

/* footer */
.footer{position:absolute;left:0;top:1087px;width:783px;height:113px}
.footer-bg{position:absolute;left:0;top:0}
.footer-info{position:absolute;left:36px;top:24px;color:var(--white)}
.footer-info p{font-size:14px;font-weight:600}
.address{display:flex;align-items:flex-start;gap:8px;margin-top:10px;font-size:14px;font-weight:700;line-height:1.2}
.address svg{flex:none;margin-top:1px}
.contact{position:absolute;left:393px;top:30px;display:flex;align-items:center;color:var(--white)}
.contact-name{font-size:21px;font-weight:600;color:var(--pink);line-height:1.1}
.phone{display:flex;align-items:center;gap:5px;font-size:17px;font-weight:700;margin-top:2px}
.phone svg{flex:none}
.contact-split{width:0;height:40px;border-left:1.5px dashed #aaa;margin:0 14px}
.links{display:flex;flex-direction:column;gap:8px;font-size:14px;font-weight:600}
.links span{display:flex;align-items:center;gap:6px}
.links svg{flex:none}
</style>
</head>
<body>
<div class="flyer">

  <header class="hero">
    <svg class="hero-bg" width="783" height="552" viewBox="0 0 783 552">
      <defs>
        <linearGradient id="parkTone" x1="0" y1="0" x2="0" y2="1">
          <stop offset="0" stop-color="#fbf7f2"/>
          <stop offset=".38" stop-color="#f5e2c6"/>
          <stop offset=".52" stop-color="#c8b07c"/>
          <stop offset=".6" stop-color="#8a8a4a"/>
          <stop offset=".8" stop-color="#7a8540"/>
          <stop offset="1" stop-color="#5f6a34"/>
        </linearGradient>
      </defs>
      <rect width="783" height="552" fill="var(--dark)"/>
      <path d="M0,158 C130,140 270,133 390,133 L440,133 C260,140 110,170 0,215 Z" fill="var(--pink)"/>
      <path d="M360,133 L470,133 C620,138 720,165 783,192 L783,262 C700,205 560,160 360,133 Z" fill="var(--grey)"/>
      <path d="M783,385 L783,552 L380,552 C560,552 700,515 783,385 Z" fill="var(--pink)"/>
      <path role="img" aria-label="Photo of two people stretching cross-legged on mats in a sunny summer park at golden hour"
            d="M0,218 C120,172 265,145 391,145 C540,145 680,185 783,262 L783,420 C690,520 540,548 391,548 C250,548 110,522 0,470 Z"
            fill="url(#parkTone)"/>
    </svg>
    <div class="brand">
      <span class="brand-dot"></span>
      <span class="brand-name">Stretch with Mira</span>
    </div>
    <h1 class="title">
      <span class="title-line1">Stretch on</span>
      <span class="title-line2">The Green with Mira</span>
      <span class="title-script">in Summer</span>
    </h1>
  </header>

  <h2 class="levels">
    <span class="levels-top">Classes are for beginners</span>
    <span class="levels-bottom">to advance levels</span>
  </h2>
  <div class="rule"></div>
  <p class="start">Classes start Monday, <em>October 17th</em></p>

  <section class="schedule">
    <div class="day">
      <div class="rings"><span></span><span></span><span></span><span></span><span></span><span></span><span></span></div>
      <div class="day-head is-pink">Monday</div>
      <div class="day-body"><div class="day-time">6PM</div><div class="day-level">Beginners</div></div>
    </div>
    <div class="day">
      <div class="rings"><span></span><span></span><span></span><span></span><span></span><span></span><span></span></div>
      <div class="day-head is-dark">Tuesday</div>
      <div class="day-body"><div class="day-time">6PM</div><div class="day-level">Intermediate</div></div>
    </div>
    <div class="day">
      <div class="rings"><span></span><span></span><span></span><span></span><span></span><span></span><span></span></div>
      <div class="day-head is-pink">Thursday</div>
      <div class="day-body"><div class="day-time">6PM</div><div class="day-level is-small">Intermediate/<br>Advance</div></div>
    </div>
    <div class="day">
      <div class="rings"><span></span><span></span><span></span><span></span><span></span><span></span><span></span></div>
      <div class="day-head is-dark">Saturday</div>
      <div class="day-body"><div class="day-time">9AM</div><div class="day-level is-small">All fitness<br>levels</div></div>
    </div>
  </section>

  <p class="about">My Pilates classes are specially designed to help improve strength and flexibility but as well will also improve<br>posture, reduce stress and develop control and endurance in the entire body.</p>
  <div class="rule-thin"></div>

  <section class="offer">
    <div class="booking">
      <h2>BOOKING ESSENTIAL</h2>
      <p>Limited numbers so I can make sure<br>the correct technique is always<br>being followed.</p>
    </div>
    <div class="divider"></div>
    <div class="price">
      <span class="price-amount">$15</span>
      <span class="price-unit">PER SESSION</span>
    </div>
    <div class="divider"></div>
    <div class="place">
      <b>Classes are</b>
      <span>outside at the</span>
      <strong>Lovely</strong>
      <strong>Local Park</strong>
    </div>
  </section>

  <footer class="footer">
    <svg class="footer-bg" width="783" height="113" viewBox="0 0 783 113">
      <rect width="783" height="113" fill="var(--dark)"/>
      <path d="M0,0 L440,0 C390,8 375,100 290,113 L0,113 Z" fill="var(--pink)"/>
    </svg>
    <div class="footer-info">
      <p>For more info or to book contact details</p>
      <div class="address">
        <svg width="14" height="20" viewBox="0 0 14 20"><path d="M7,0 C3,0 0,3 0,7 C0,12 7,20 7,20 C7,20 14,12 14,7 C14,3 11,0 7,0 Z" fill="#fff"/><circle cx="7" cy="7" r="2.6" fill="var(--pink)"/></svg>
        <span>Tolmore field. 12 Rawhiti St.<br>Sandringham</span>
      </div>
    </div>
    <div class="contact">
      <div>
        <div class="contact-name">Mira</div>
        <div class="phone">
          <svg width="12" height="12" viewBox="0 0 24 24"><path d="M6.6 10.8a15.1 15.1 0 0 0 6.6 6.6l2.2-2.2a1 1 0 0 1 1-.25 11.4 11.4 0 0 0 3.6.57 1 1 0 0 1 1 1V20a1 1 0 0 1-1 1A17 17 0 0 1 3 4a1 1 0 0 1 1-1h3.5a1 1 0 0 1 1 1c0 1.25.2 2.45.57 3.57a1 1 0 0 1-.25 1Z" fill="var(--pink)"/></svg>
          <span>027385116</span>
        </div>
      </div>
      <div class="contact-split"></div>
      <div class="links">
        <span><svg width="10" height="8" viewBox="0 0 10 8"><rect width="10" height="8" rx="1" fill="var(--pink)"/><path d="M0,1 L5,5 L10,1" stroke="#fff" stroke-width="1" fill="none"/></svg>mira@stretchwithmira.net</span>
        <span><svg width="10" height="10" viewBox="0 0 10 10"><circle cx="5" cy="5" r="4.3" stroke="var(--pink)" stroke-width="1.2" fill="none"/><path d="M0.7,5 H9.3 M5,0.7 V9.3" stroke="var(--pink)" stroke-width="1"/></svg>www.stretchwithmira.net</span>
      </div>
    </div>
  </footer>

</div>
</body>
</html>
```